BRN website video quote promotion tiles

We are promoting vehicle leasing by video, which contains several quotation examples imported from the video. We must re-vamp the quotation tiles, contact boxes, and contact form. The first tile is generated from the video, so this must be a separate project. We are looking for a welcoming, professional flow and leave color choices to design with an emphasis on communication prompts, and additional prompts in the design would be welcome.

Target Market(s)

Any Customer interaction from the tile quotes, contact, call, message,

Industry/Entity Type

vehicle leasing

Coding

Coded - Design and coding required

Number of Pages Required

1 page

Colors

Designer to choose colors to be used in the design.

Requirements
Must have
• emphasis on point of contact and visual impact on quote tile excluding main one
Should not have
• changes to the quote structure as these imported from video pricing no changes to main image as this template which can addressed as separate project

```html
<!DOCTYPE html>
<html lang="en">
<head>
<meta charset="utf-8">
<title>Contract Hire Quote Tiles</title>
<link rel="stylesheet" href="https://fonts.googleapis.com/css2?family=Fira+Sans:wght@400;500;600;700&family=Righteous&family=Merriweather:wght@400;700;900&family=Oswald:wght@400;500&family=Marcellus&display=swap">
<style>
:root{
  --page:#f7f7f7;
  --tile-grey:#f3f3f3;
  --orange:#e08134;
  --green:#7dd172;
  --yellow:#ecbe40;
  --red:#d8292f;
  --chat-green:#47b94f;
  --ink:#111111;
  --white:#ffffff;
  --muted:#8a8a8a;
}
*{box-sizing:border-box;margin:0;padding:0}
html,body{width:1200px;height:917px;overflow:hidden}
body{
  position:relative;
  background:radial-gradient(ellipse at 30% 40%,#ffffff 0%,var(--page) 60%,#efefef 100%);
  font-family:"Fira Sans",sans-serif;color:var(--ink);
}
svg{display:block}
.tile{position:absolute;top:50px;text-align:center}
.btn{position:absolute;display:flex;align-items:center;text-decoration:none;color:var(--white)}
.btn-icon{flex:none;display:flex;align-items:center;justify-content:center;border-radius:50%;background:var(--white)}

/* tile one */
.tile-classic{left:48px;width:357px;height:264px;background:var(--tile-grey);
  border-radius:0 0 70px 0;box-shadow:0 1px 6px rgba(0,0,0,.18)}
.tile-classic .title{position:absolute;top:27px;width:100%;font-family:"Righteous",sans-serif;font-weight:400;font-size:22px;color:var(--orange);letter-spacing:.3px}
.tile-classic .price{position:absolute;left:113px;top:64px;width:130px;height:50px;background:var(--yellow);
  border-radius:4px 4px 22px 4px;font-size:22px;font-weight:600;line-height:50px}
.tile-classic .terms{position:absolute;top:123px;width:100%;font-size:19px}
.tile-classic .note{position:absolute;top:150px;width:100%;font-size:13px;font-weight:600;color:var(--red)}
.tile-classic .btn-contact{left:39px;top:187px;width:186px;height:50px;background:var(--orange);border-radius:25px 14px 14px 25px;font-size:19px;font-weight:600}
.tile-classic .btn-contact .btn-icon{width:51px;height:51px;background:var(--red);margin-left:-1px;margin-right:6px}
.tile-classic .btn-chat{left:235px;top:183px;width:62px;height:62px;border-radius:50%;border:2px solid var(--chat-green);background:var(--white);justify-content:center}

/* tile two */
.tile-bold{left:421px;width:356px;height:262px;background:var(--orange);border-radius:28px;color:var(--white);font-family:"Merriweather",serif}
.tile-bold .title{position:absolute;left:20px;top:36px;text-align:left;font-size:25px;line-height:30px;font-weight:400}
.tile-bold .title b{font-weight:900}
.tile-bold .price{position:absolute;left:199px;top:40px;width:129px;height:49px;border:2px solid var(--white);border-radius:25px;font-size:22px;line-height:45px}
.tile-bold .terms{position:absolute;top:116px;width:100%;font-size:19px;font-weight:700}
.tile-bold .note{position:absolute;top:146px;width:100%;font-size:14px}
.tile-bold .btn{top:188px;width:155px;height:51px;border:2px solid var(--white);border-radius:26px;font-size:15px;font-weight:700;font-family:"Merriweather",serif}
.tile-bold .btn .btn-icon{width:43px;height:43px;margin:0 6px 0 2px}
.tile-bold .btn-contact{left:15px}
.tile-bold .btn-chat{left:177px}

/* tile three */
.tile-fresh{left:792px;width:357px;height:262px;background:var(--green);border-radius:38px 38px 38px 0}
.tile-fresh .title{position:absolute;top:20px;width:100%;font-family:"Marcellus",serif;font-size:28px;font-weight:700}
.tile-fresh .price{position:absolute;left:113px;top:61px;width:131px;height:50px;background:var(--white);border-radius:25px;
  box-shadow:3px 3px 0 var(--ink);font-size:22px;font-weight:600;line-height:50px}
.tile-fresh .terms{position:absolute;top:125px;width:100%;font-family:"Oswald",sans-serif;font-size:21px}
.tile-fresh .note{position:absolute;top:156px;width:100%;font-size:13px;font-weight:600}
.tile-fresh .btn{top:184px;width:155px;height:51px;background:var(--orange);border-radius:26px;box-shadow:2px 3px 0 var(--ink);font-size:16px;font-weight:600}
.tile-fresh .btn .btn-icon{width:43px;height:43px;margin:0 9px 0 4px}
.tile-fresh .btn-contact{left:19px}
.tile-fresh .btn-chat{left:181px}

/* contact form */
.contact-form{position:absolute;left:56px;top:366px;width:1088px;height:503px}
.form-header{height:45px;background:var(--orange);color:var(--white);font-size:19px;font-weight:400;padding-left:28px;line-height:45px;position:relative}
.form-close{position:absolute;right:23px;top:13px;width:19px;height:19px;border-radius:50%;background:var(--white);display:flex;align-items:center;justify-content:center}
.form-body{position:absolute;top:45px;left:0;width:1088px;height:458px;
  background:linear-gradient(120deg,#5e635c 0%,#6f716c 30%,#595650 60%,#3b3835 85%,#2d2b29 100%)}
.field{position:absolute;background:var(--white);border-radius:4px;display:flex;align-items:center;gap:5px;padding-left:16px;font-size:10.5px;color:var(--muted)}
.field.first{left:44px;top:59px;width:489px;height:62px}
.field.last{left:545px;top:59px;width:489px;height:62px}
.field.email{left:44px;top:135px;width:489px;height:62px}
.field.phone{left:545px;top:135px;width:489px;height:62px}
.field.message{left:44px;top:210px;width:994px;height:137px;align-items:flex-start;padding-top:21px}
.submit{position:absolute;left:45px;top:363px;width:131px;height:50px;background:var(--yellow);border:none;border-radius:3px;
  font-family:"Fira Sans",sans-serif;font-size:15px;font-weight:600;color:var(--ink)}
</style>
</head>
<body>

<section class="tile tile-classic">
  <h2 class="title">CONTRACT HIRE</h2>
  <div class="price">£247.33</div>
  <p class="terms">3 Years, 9+35, 10k miles Annualy</p>
  <p class="note">(Not Maintained)</p>
  <a class="btn btn-contact" href="#contact">
    <span class="btn-icon">
      <svg width="28" height="28" viewBox="0 0 24 24" fill="none" stroke="#fff" stroke-width="1.4"><path d="M5 12a7 7 0 0 1 14 0"/><rect x="3.5" y="11" width="3" height="5" rx="1"/><rect x="17.5" y="11" width="3" height="5" rx="1"/><path d="M6 20c1.5-2 3.5-3 6-3s4.5 1 6 3"/><path d="M19 16c0 2-2 3-5 3"/></svg>
    </span>CONTACT US</a>
  <a class="btn btn-chat" href="#chat">
    <svg width="42" height="42" viewBox="0 0 24 24"><circle cx="12" cy="12" r="11" fill="#47b94f"/><path d="M8.5 7.5c.5-.5 1.3-.4 1.6.2l.8 1.6c.2.4.1.9-.2 1.2l-.6.6c.6 1.3 1.6 2.3 2.9 2.9l.6-.6c.3-.3.8-.4 1.2-.2l1.6.8c.6.3.7 1.1.2 1.6l-.8.8c-2.5 1.5-8.4-4.4-6.9-6.9z" fill="#fff"/></svg>
  </a>
</section>

<section class="tile tile-bold">
  <h2 class="title"><b>CONTRACT</b><br>HIRE</h2>
  <div class="price">£247.33</div>
  <p class="terms">3 Years, 9+35, 10k miles Annualy</p>
  <p class="note">(Not Maintained)</p>
  <a class="btn btn-contact" href="#contact">
    <span class="btn-icon"><svg width="26" height="26" viewBox="0 0 24 24" fill="none" stroke="#222" stroke-width="1.3"><path d="M5 12a7 7 0 0 1 14 0"/><rect x="3.5" y="11" width="3" height="5" rx="1"/><rect x="17.5" y="11" width="3" height="5" rx="1"/><path d="M6 20c1.5-2 3.5-3 6-3s4.5 1 6 3"/></svg></span>CONTACT US</a>
  <a class="btn btn-chat" href="#chat">
    <span class="btn-icon"><svg width="34" height="34" viewBox="0 0 24 24"><circle cx="12" cy="12" r="11" fill="#47b94f"/><path d="M8.5 7.5c.5-.5 1.3-.4 1.6.2l.8 1.6c.2.4.1.9-.2 1.2l-.6.6c.6 1.3 1.6 2.3 2.9 2.9l.6-.6c.3-.3.8-.4 1.2-.2l1.6.8c.6.3.7 1.1.2 1.6l-.8.8c-2.5 1.5-8.4-4.4-6.9-6.9z" fill="#fff"/></svg></span>CHATLINE</a>
</section>

<section class="tile tile-fresh">
  <h2 class="title">CONTRACT HIRE</h2>
  <div class="price">£247.33</div>
  <p class="terms">3 Years, 9+35, 10k miles Annualy</p>
  <p class="note">(Not Maintained)</p>
  <a class="btn btn-contact" href="#contact">
    <span class="btn-icon"><svg width="26" height="26" viewBox="0 0 24 24" fill="none" stroke="#222" stroke-width="1.3"><path d="M5 12a7 7 0 0 1 14 0"/><rect x="3.5" y="11" width="3" height="5" rx="1"/><rect x="17.5" y="11" width="3" height="5" rx="1"/><path d="M6 20c1.5-2 3.5-3 6-3s4.5 1 6 3"/></svg></span>CONTACT US</a>
  <a class="btn btn-chat" href="#chat">
    <span class="btn-icon"><svg width="34" height="34" viewBox="0 0 24 24"><circle cx="12" cy="12" r="11" fill="#47b94f"/><path d="M8.5 7.5c.5-.5 1.3-.4 1.6.2l.8 1.6c.2.4.1.9-.2 1.2l-.6.6c.6 1.3 1.6 2.3 2.9 2.9l.6-.6c.3-.3.8-.4 1.2-.2l1.6.8c.6.3.7 1.1.2 1.6l-.8.8c-2.5 1.5-8.4-4.4-6.9-6.9z" fill="#fff"/></svg></span>CHATLINE</a>
</section>

<section class="contact-form" id="contact">
  <header class="form-header">Please Submit Your Contact Details
    <span class="form-close"><svg width="11" height="11" viewBox="0 0 11 11"><path d="M2 2l7 7M9 2l-7 7" stroke="#e08134" stroke-width="2" stroke-linecap="round"/></svg></span>
  </header>
  <div class="form-body" role="img" aria-label="Background photo of hands holding a smartphone with contact icons overlay">
    <label class="field first"><svg width="11" height="11" viewBox="0 0 12 12" fill="none" stroke="#777" stroke-width="1.2"><circle cx="6" cy="4" r="2.5"/><path d="M1.5 11.5c0-2.5 2-4 4.5-4s4.5 1.5 4.5 4z"/></svg>Firest Name</label>
    <label class="field last"><svg width="11" height="11" viewBox="0 0 12 12" fill="none" stroke="#777" stroke-width="1.2"><circle cx="6" cy="4" r="2.5"/><path d="M1.5 11.5c0-2.5 2-4 4.5-4s4.5 1.5 4.5 4z"/></svg>Last Name</label>
    <label class="field email"><svg width="11" height="11" viewBox="0 0 12 12" fill="none" stroke="#777" stroke-width="1.2"><rect x="1" y="2.5" width="10" height="7" rx="1"/><path d="M1 3l5 3.5L11 3"/></svg>Email</label>
    <label class="field phone"><svg width="11" height="11" viewBox="0 0 12 12"><path d="M2.5 1l2 .3.8 2.3-1.2 1c.6 1.3 1.6 2.3 2.9 2.9l1-1.2 2.3.8.3 2c-.1.6-.6 1-1.2 1C5 10.8 1.2 7 1.5 2.2c0-.6.4-1.1 1-1.2z" fill="#777"/></svg>Contact Number</label>
    <label class="field message"><svg width="12" height="11" viewBox="0 0 12 11" fill="none" stroke="#777" stroke-width="1"><rect x=".5" y=".5" width="8" height="6"/><path d="M3.5 6.5v2h6l1.5 1.5V3.5H8.5"/></svg>Your Message</label>
    <button class="submit" type="submit">SUBMIT</button>
  </div>
</section>

</body>
</html>
```